The Visual Personality of Miss Cobbler Food Trailer

Something that stands out with color and our logo. This is a food trailer that attends several events in the spring and summer. We are known for being one of the best Gumbo producers in mid Michigan. We have been responsible for connecting different communities and cultures together and we are strong supporters of our veterans since this is a veteran owned business. All of our vegetables are fresh and locally purchased. These recipes are originally from New Orleans Louisiana. Our website is Misscobbler.net. This will be used for an 8" x 11" poster. Leave a box or area that states "WHERE WE WILL BE:" so that we can add the location of the event that we are attending.

Target Market(s)

We do cuisine that is recognized in the southern states of the USA. but live in the northern part of the USA. We are providing a menu of different southern recipes so they do not have to go all the way down south for get..

Industry/Entity Type

Food/Restaurant Industry

Font styles to use
Serif
Decorative

Colors
0094D4
00A9DD
6FCCEA
C7EBF8
E9F6FB
59FF00
82FF00
B8FF75
E3FFCB
F4FFEA
FFF300
FFF600
FEFA6F
FFFEC7
FFFEE8
EE7325
F08F49
F5BC92
FAE3D3
FDF4ED
EB3D1F
EC4F4E
F09395
F8D3D4
FCEDEE
A7469A
B969AE
D3A5CF
EDDBEB
F8F0F9

Requirements
Must have
• Our logo, which is "Miss Cobbler", "Homemade Deliciousness". We need an area on the poster where we can manually add the location of the event we will be attending because it changes weekly. location
Nice to have
• Bold colors and logo

```html
<!DOCTYPE html>
<html lang="en">
<head>
<meta charset="utf-8">
<title>Miss Cobbler Food Trailer Poster</title>
<link rel="stylesheet" href="https://fonts.googleapis.com/css2?family=Roboto+Slab:wght@400;600;700&family=Lato:wght@300&display=swap">
<style>
  :root {
    --red: #e8251b;
    --red-deep: #e0201a;
    --orange: #f2693a;
    --orange-light: #f58a52;
    --white: #ffffff;
    --ink: #2a2222;
    --label-red: #c8181e;
    --address-grey: #b9b9b9;
    --photo-dark: #8b8f99;
    --photo-warm: #d89a5a;
    --photo-light: #e9dcc4;
  }
  * { box-sizing: border-box; margin: 0; padding: 0; }
  html, body {
    width: 848px;
    height: 1200px;
    overflow: hidden;
    background: var(--white);
  }
  .poster {
    position: relative;
    width: 848px;
    height: 1200px;
    overflow: hidden;
    font-family: "Roboto Slab", serif;
  }
  .hero-photo {
    position: absolute;
    inset: 0;
    background:
      radial-gradient(ellipse 60% 35% at 55% 48%, #e27a48 0%, rgba(226,122,72,0) 70%),
      radial-gradient(ellipse 55% 25% at 45% 30%, var(--photo-warm) 0%, rgba(216,154,90,0) 75%),
      linear-gradient(170deg, var(--photo-dark) 0%, var(--photo-light) 30%, #c9a07a 55%, #9a9aa2 100%);
  }
  .diagonal-rule {
    position: absolute;
    inset: 0;
    background: var(--white);
    clip-path: polygon(0 494px, 848px 925px, 848px 1200px, 0 1200px);
  }
  .color-field {
    position: absolute;
    inset: 0;
    background: linear-gradient(120deg, var(--red-deep) 0%, var(--red) 35%, var(--orange) 75%, var(--orange-light) 100%);
    clip-path: polygon(0 508px, 848px 939px, 848px 1200px, 0 1200px);
  }
  .web-band {
    position: absolute;
    top: 0;
    left: 717px;
    width: 131px;
    height: 1200px;
    background: linear-gradient(180deg, rgba(255,255,255,0.38) 0%, rgba(255,225,215,0.3) 50%, rgba(255,150,100,0.35) 100%);
  }
  .web-address {
    position: absolute;
    left: 800px;
    top: 598px;
    transform: translate(-50%, -50%) rotate(-90deg);
    font-family: "Lato", sans-serif;
    font-weight: 300;
    font-size: 30px;
    letter-spacing: 26px;
    color: var(--white);
    white-space: nowrap;
  }
  .brand-badge {
    position: absolute;
    left: 43px;
    top: 72px;
    width: 168px;
    height: 168px;
    border-radius: 50%;
    background: var(--white);
    display: flex;
    align-items: center;
    justify-content: center;
    text-align: center;
  }
  .brand-name {
    font-weight: 700;
    font-size: 25px;
    line-height: 1.15;
    letter-spacing: 1px;
    text-transform: uppercase;
    color: var(--ink);
  }
  .veg-sketch {
    position: absolute;
    background: rgba(255,255,255,0.12);
  }
  .veg-sketch.tomato { left: -20px; top: 605px; width: 56px; height: 56px; border-radius: 50%; }
  .veg-sketch.herb { left: 150px; top: 620px; width: 40px; height: 100px; border-radius: 20px; background: rgba(170,110,40,0.3); }
  .veg-sketch.carrot { left: 555px; top: 872px; width: 80px; height: 130px; border-radius: 40px; }
  .veg-sketch.broccoli { left: 722px; top: 1078px; width: 112px; height: 98px; border-radius: 48px; }
  .mission {
    position: absolute;
    left: 59px;
    top: 766px;
    width: 410px;
    color: var(--white);
    font-weight: 600;
    font-size: 14px;
    line-height: 29px;
    letter-spacing: 2.2px;
    text-transform: uppercase;
  }
  .mission-line {
    display: block;
    white-space: nowrap;
    text-align: justify;
    text-align-last: justify;
  }
  .mission-line:last-child { text-align-last: left; }
  .location-box {
    position: absolute;
    left: 49px;
    top: 987px;
    width: 429px;
    height: 152px;
    border-radius: 26px;
    background: var(--white);
  }
  .location-label {
    position: absolute;
    left: 33px;
    top: 24px;
    font-weight: 700;
    font-size: 17px;
    letter-spacing: 0.5px;
    color: var(--label-red);
    text-transform: uppercase;
  }
  .location-address {
    position: absolute;
    left: 69px;
    top: 64px;
    font-weight: 700;
    font-size: 17px;
    letter-spacing: 1.5px;
    color: var(--address-grey);
    text-transform: uppercase;
  }
  .pepper-art {
    position: absolute;
    left: 424px;
    top: 1048px;
    width: 170px;
    height: 80px;
    border-radius: 40px;
    background: linear-gradient(100deg, #e8321e 0%, #f4a040 100%);
    opacity: 0.85;
  }
</style>
</head>
<body>
<main class="poster">
  <div class="hero-photo" role="img" aria-label="Photo of a po'boy sandwich with tomato, lettuce and remoulade beside potato chips"></div>
  <div class="diagonal-rule"></div>
  <div class="color-field"></div>
  <div class="veg-sketch tomato" role="img" aria-label="Faint line sketch of a tomato"></div>
  <div class="veg-sketch herb" role="img" aria-label="Small sprig of herbs"></div>
  <div class="veg-sketch carrot" role="img" aria-label="Faint line sketch of a carrot"></div>
  <div class="veg-sketch broccoli" role="img" aria-label="Faint line sketch of broccoli"></div>

  <div class="web-band"></div>
  <div class="web-address">www.misscobbler.net</div>

  <div class="brand-badge">
    <div class="brand-name">Miss<br>Cobbler</div>
  </div>

  <p class="mission">
    <span class="mission-line">We prepare and serve amazing</span>
    <span class="mission-line">high quality, delicious southern</span>
    <span class="mission-line">food at an affordable price. We</span>
    <span class="mission-line">want to provide our customers</span>
    <span class="mission-line">with the most authentic</span>
    <span class="mission-line">Louisiana experience outside of</span>
    <span class="mission-line">Louisiana.</span>
  </p>

  <section class="location-box">
    <h2 class="location-label">Where we will be</h2>
    <p class="location-address">Your address here</p>
  </section>
  <div class="pepper-art" role="img" aria-label="Illustration of red and orange chili peppers"></div>
</main>
</body>
</html>
```